KRV Business Card

Looking for a business card for my restaurant group I own. Four different concepts:

Copperfield Alehouse
Bristow Alehouse
Tanager's Stone Hearth Kitchen
Pellston Patty Company

Card doesn't need to include all the logos.

```html
<!DOCTYPE html>
<html lang="en">
<head>
<meta charset="UTF-8">
<title>KRV Business Card</title>
<link href="https://fonts.googleapis.com/css2?family=Poppins:ital,wght@0,400;0,500;0,600;1,400&display=swap" rel="stylesheet">
<style>
  :root {
    --backdrop: #232323;
    --card-white: #ffffff;
    --gold: #d2af6b;
    --ink: #4a4a4a;
    --ink-soft: #6b6b6b;
    --rule: #8a8a8a;
  }
  * { margin: 0; padding: 0; box-sizing: border-box; }
  html, body {
    width: 1125px;
    height: 1200px;
    overflow: hidden;
    background: var(--backdrop);
    font-family: "Poppins", sans-serif;
  }
  .card {
    position: absolute;
    left: 171px;
    width: 826px;
    height: 472px;
  }
  .card--front { top: 106px; background: var(--card-white); }
  .card--back  { top: 639px; background: var(--gold); }

  .contact {
    position: absolute;
    left: 45px;
    top: 52px;
    color: var(--ink);
  }
  .contact__name {
    font-size: 31px;
    font-weight: 600;
    color: var(--gold);
    line-height: 1.15;
  }
  .contact__title {
    font-size: 22px;
    color: var(--ink-soft);
    line-height: 1.2;
  }
  .contact__email {
    font-size: 21px;
    font-style: italic;
    line-height: 1.25;
  }
  .contact__rule {
    width: 287px;
    border-top: 2px dotted var(--rule);
    margin: 26px 0 34px;
  }
  .contact__lines {
    font-size: 20.5px;
    line-height: 27px;
  }

  .brand-name {
    position: absolute;
    left: 420px;
    width: 385px;
    top: 180px;
    text-align: center;
    color: var(--gold);
    font-weight: 500;
    font-size: 38px;
    line-height: 1.25;
    letter-spacing: 5px;
    text-transform: uppercase;
  }

  .back__mark {
    position: absolute;
    left: 0;
    right: 0;
    top: 100px;
    text-align: center;
    color: var(--card-white);
    font-weight: 600;
    font-size: 175px;
    line-height: 1;
    letter-spacing: 6px;
  }
  .back__url {
    position: absolute;
    left: 0;
    right: 0;
    top: 392px;
    text-align: center;
    color: var(--card-white);
    font-size: 19px;
    letter-spacing: 4.5px;
    text-transform: uppercase;
  }
</style>
</head>
<body>
  <section class="card card--front">
    <div class="contact">
      <div class="contact__name">Daniel Hart</div>
      <div class="contact__title">President</div>
      <div class="contact__email">info@kestrelridge.com</div>
      <div class="contact__rule"></div>
      <div class="contact__lines">
        Tel: 555-214-7730<br>
        Fax: 555-318-4062<br>
        Mob: 555-407-1195
      </div>
      <div class="contact__rule"></div>
      <div class="contact__lines">
        4120 Larkspur Court<br>
        Juneau, Alaska 99801<br>
        www.kestrelridge.com
      </div>
    </div>
    <div class="brand-name">Kestrel Ridge<br>Ventures</div>
  </section>

  <section class="card card--back">
    <div class="back__mark">KRV</div>
    <div class="back__url">www.kestrelridge.com</div>
  </section>
</body>
</html>
```